Podcast Cover Art Design for Divorce Support

Need a podcast cover art design for new podcast that will cover Emotional Divorce Support and Recovery topics. People are lost, confused. They are looking for help during the confusion and heartbreak. Main Title is "Quiet Harbor Podcast". Subtitle is "Finding Your Steady Ground". We want a design that is encouraging yet not overly "happy". We also want to convey kindness, clarity, and strength, if possible. Our logo colors use grey and red though we aren't tied to those colors for the podcast. Logo may be used on the podcast but not required. Final image should be 3000x3000px. Our logo uses Montserrat-Medium and Multi-SemiBold. Not necessary but available if you want to use it.

```html
<!DOCTYPE html>
<html lang="en">
<head>
<meta charset="utf-8">
<title>Quiet Harbor Podcast — Cover Art</title>
<link rel="stylesheet" href="https://fonts.googleapis.com/css2?family=Oswald:wght@500;700&family=Yellowtail&display=swap">
<style>
  :root {
    --page-bg: #e4e8ee;
    --cover-light: #ffffff;
    --cover-mid: #eeeeee;
    --cover-grey: #d9d9d9;
    --brand-red: #e30613;
    --ink: #0a0a0a;
    --paper: #ffffff;
  }
  * { margin: 0; padding: 0; box-sizing: border-box; }
  html, body {
    width: 1200px;
    height: 840px;
    overflow: hidden;
    background: var(--page-bg);
  }
  .cover {
    position: absolute;
    left: 210px;
    top: 30px;
    width: 780px;
    height: 780px;
    overflow: hidden;
    background:
      radial-gradient(ellipse at 50% 35%, var(--cover-light) 0%, var(--cover-mid) 60%, var(--cover-grey) 100%);
    box-shadow: 0 14px 30px rgba(40, 50, 70, 0.18);
  }
  .cover__texture {
    position: absolute;
    inset: 0;
    background: linear-gradient(180deg, rgba(255,255,255,0.6) 0%, rgba(255,255,255,0) 55%, rgba(200,200,200,0.35) 100%);
  }
  .cover__heart {
    position: absolute;
    left: 105px;
    top: 74px;
    width: 560px;
    height: 541px;
    border-radius: 45% 45% 50% 50% / 40% 40% 60% 60%;
    background: radial-gradient(ellipse at 50% 45%, rgba(227,6,19,0) 55%, rgba(227,6,19,0.22) 70%, rgba(227,6,19,0) 80%);
  }
  .title {
    position: absolute;
    left: 0;
    width: 100%;
    text-align: center;
    line-height: 1;
  }
  .title__main {
    top: 185px;
    left: 10px;
    font-family: "Oswald", sans-serif;
    font-weight: 700;
    font-size: 122px;
    color: var(--ink);
    letter-spacing: 1px;
  }
  .title__script {
    top: 300px;
    left: 10px;
    font-family: "Yellowtail", cursive;
    font-size: 112px;
    color: var(--brand-red);
    transform: rotate(-4deg);
  }
  .title__label {
    top: 468px;
    left: 10px;
    font-family: "Oswald", sans-serif;
    font-weight: 700;
    font-size: 40px;
    letter-spacing: 3px;
    color: var(--ink);
  }
  .band {
    position: absolute;
    left: 0;
    bottom: 0;
    width: 780px;
    height: 180px;
  }
  .band__tagline {
    position: absolute;
    left: 0;
    bottom: 38px;
    width: 100%;
    text-align: center;
    font-family: "Oswald", sans-serif;
    font-weight: 500;
    font-size: 48px;
    letter-spacing: 1px;
    color: var(--paper);
    line-height: 1;
  }
</style>
</head>
<body>
  <main class="cover">
    <div class="cover__texture" role="img" aria-label="Soft light grey faceted triangle background"></div>
    <div class="cover__heart" role="img" aria-label="Red brush-stroke heart outline framing the title"></div>

    <h1 class="title title__main">Quiet</h1>
    <p class="title title__script">Harbor</p>
    <p class="title title__label">Podcast</p>

    <svg class="band" viewBox="0 0 780 180" preserveAspectRatio="none" aria-hidden="true">
      <path d="M0 48 L30 44 L60 40 L90 42 L120 36 L150 40 L170 34 L200 36 L230 30 L260 34 L290 24 L320 20 L350 14 L380 8 L400 12 L420 6 L445 14 L470 18 L500 20 L530 16 L560 22 L590 20 L620 24 L650 26 L690 22 L720 26 L750 24 L780 20 L780 180 L0 180 Z" fill="#ffffff"/>
      <path d="M0 54 L30 50 L60 46 L90 48 L120 42 L150 46 L170 40 L200 42 L230 36 L260 40 L290 30 L320 26 L350 20 L380 14 L400 18 L420 12 L445 20 L470 24 L500 26 L530 22 L560 28 L590 26 L620 30 L650 32 L690 28 L720 32 L750 30 L780 26 L780 180 L0 180 Z" fill="var(--brand-red)"/>
    </svg>
    <p class="band__tagline">Finding Your Steady Ground</p>
  </main>
</body>
</html>
```